Brightfen Business Card Redesign & Logo Update

We need to update our business cards to something more modern and fresh. Brightfen can provide the current color schemes and old design examples, but welcome creativity in helping us with this redesign. PLEASE NOTE that we no longer utilize the "tree" and/or "leaf" imagery in our branding. If able would apprecaite an update on the quality of our "words only" logo in Ai. / PNG formats too.

Target Market(s)

Investors, landowners, corporate partners, contractors

Industry/Entity Type

Environmental Restoration & Conservation

Contact Information for Business Card

Logo, persons name, title, mailing address, phone and email, website url

Font styles to use
Other font styles liked:
• Merriweather

Requirements
Nice to have
• Logo, persons name, title, mailing address, phone and email, website url, but open to ideams
Should not have
• No all back backgrounds

```html
<!DOCTYPE html>
<html lang="en">
<head>
<meta charset="utf-8">
<title>Brightfen Business Cards</title>
<link rel="stylesheet" href="https://fonts.googleapis.com/css2?family=Montserrat:wght@400;500;600;700;800&display=swap">
<style>
  :root {
    --green: #167a3a;
    --orange: #ee7f24;
    --white: #ffffff;
    --ink: #2b2b2b;
    --backdrop-top: #d2d2d2;
    --backdrop-bottom: #a7a7a7;
    --tile: #dcdde1;
  }
  * { margin: 0; padding: 0; box-sizing: border-box; }
  html, body { width: 1200px; height: 788px; overflow: hidden; }
  body {
    position: relative;
    font-family: "Montserrat", Arial, sans-serif;
    background: linear-gradient(180deg, var(--backdrop-top), var(--backdrop-bottom));
  }
  .card {
    position: absolute;
    top: 150px;
    width: 520px;
    height: 297px;
    box-shadow: 0 14px 30px rgba(0,0,0,0.25);
  }
  .card--front { left: 50px; background: var(--white); }
  .card--back { left: 630px; background: var(--orange); }

  .brand { position: absolute; left: 0; right: 0; text-align: center; }
  .brand__name {
    font-weight: 800;
    letter-spacing: 2px;
    line-height: 1;
  }
  .brand__tagline {
    font-weight: 600;
    letter-spacing: 1.2px;
    margin-top: 6px;
  }
  .card--front .brand { top: 38px; }
  .card--front .brand__name { font-size: 40px; color: var(--green); }
  .card--front .brand__tagline { font-size: 9.5px; color: var(--green); }

  .card--back .brand { top: 108px; }
  .card--back .brand__name { font-size: 56px; color: var(--white); }
  .card--back .brand__tagline { font-size: 13px; color: var(--white); margin-top: 8px; }

  .person { position: absolute; left: 58px; top: 146px; width: 200px; text-align: right; }
  .person__name { font-size: 20px; font-weight: 700; letter-spacing: 1px; line-height: 1.1; }
  .person__first { color: var(--green); }
  .person__last { color: var(--orange); }
  .person__title { font-size: 12.5px; color: var(--ink); margin-top: 4px; }

  .divider { position: absolute; left: 272px; top: 140px; width: 1px; height: 66px; background: var(--green); }

  .contact { position: absolute; left: 288px; top: 140px; list-style: none; }
  .contact__item {
    display: flex; align-items: center; gap: 7px;
    font-size: 12px; color: var(--ink); line-height: 22px;
  }
  .contact__icon { width: 10px; height: 10px; flex: none; }

  .address {
    position: absolute; left: 0; right: 0; bottom: 32px;
    text-align: center; font-size: 12px; color: var(--ink); letter-spacing: 0.3px;
  }

  .logo-tile {
    position: absolute; right: 0; bottom: 0;
    width: 376px; height: 128px; background: var(--tile);
    display: flex; flex-direction: column; align-items: center; justify-content: center;
  }
  .logo-tile .brand { position: static; }
  .logo-tile .brand__name { font-size: 40px; color: var(--green); }
  .logo-tile .brand__tagline { font-size: 10.5px; color: var(--green); }
</style>
</head>
<body>
  <section class="card card--front" aria-label="Business card front">
    <div class="brand">
      <div class="brand__name">BRIGHTFEN</div>
      <div class="brand__tagline">ENVIRONMENTAL CREDIT COMPANY</div>
    </div>

    <div class="person">
      <div class="person__name"><span class="person__first">MARCUS</span> <span class="person__last">ELLERY</span></div>
      <div class="person__title">CEO/Founder</div>
    </div>

    <div class="divider"></div>

    <ul class="contact">
      <li class="contact__item">
        <svg class="contact__icon" viewBox="0 0 10 10"><path d="M2 0.5 L3.6 2.6 L2.7 3.6 Q3.6 5.8 6.4 7.3 L7.4 6.4 L9.5 8 L8.3 9.5 Q2 8.5 0.5 1.7 Z" fill="var(--orange)"/></svg>
        (555) 010 2468
      </li>
      <li class="contact__item">
        <svg class="contact__icon" viewBox="0 0 10 10"><rect x="0.5" y="2" width="9" height="6.5" fill="var(--orange)"/><path d="M0.5 2 L5 5.8 L9.5 2" fill="none" stroke="var(--white)" stroke-width="0.9"/></svg>
        Marcus@brightfen.com
      </li>
      <li class="contact__item">
        <svg class="contact__icon" viewBox="0 0 10 10"><circle cx="5" cy="5" r="4.5" fill="var(--orange)"/><path d="M0.5 5 H9.5 M5 0.5 Q2.5 5 5 9.5 M5 0.5 Q7.5 5 5 9.5" fill="none" stroke="var(--white)" stroke-width="0.7"/></svg>
        www.brightfen.com
      </li>
    </ul>

    <p class="address">48 Alder Mill Road Country Name, AB 30917</p>
  </section>

  <section class="card card--back" aria-label="Business card back">
    <div class="brand">
      <div class="brand__name">BRIGHTFEN</div>
      <div class="brand__tagline">ENVIRONMENTAL CREDIT COMPANY</div>
    </div>
  </section>

  <aside class="logo-tile" aria-label="Wordmark">
    <div class="brand">
      <div class="brand__name">BRIGHTFEN</div>
      <div class="brand__tagline">ENVIRONMENTAL CREDIT COMPANY</div>
    </div>
  </aside>
</body>
</html>
```